Mortgage Specialist Wordpress Build

I have a current WordPress site but I would like a whole new site built using the same domain. I've included a site for reference in my outline. The main focus of the website is to educate and capture leads.
I would like my blogs to stay for SEO already earned. Please see work requested attached.
Updates
Project Deadline Extended Reason: I am extending the deadline because I didn't realize this was a design only and I need the website coded as well. I've purchased the add-on. This is my first time using Pixel Harbor so please bare with me. I have additional Wordpress sites I want to have built too. Thanks, Colin Added Tuesday, April 18, 2017
Target Market(s)
Home Buyers, Home owners looking to refinance or renew their mortgages
Industry/Entity Type
Mortgage
Coding
Coded - Design and coding required
Font styles to use
Look and feel
Each slider illustrates characteristics of the customer's brand and the style your logo design should communicate.

```html
<!DOCTYPE html>
<html lang="en">
<head>
<meta charset="utf-8">
<title>Harborline Lending – Mortgage Specialist</title>
<link rel="stylesheet" href="https://fonts.googleapis.com/css2?family=Merriweather:wght@400;700&family=Open+Sans:wght@400;600&display=swap">
<style>
:root{
  --navy:#0a3a80;
  --navy-dark:#073070;
  --gold:#e8c84a;
  --ink:#333;
  --muted:#8a8a8a;
  --card:#e9edf3;
  --band:#ebebeb;
  --foot:#f0f0f0;
  --white:#fff;
}
*{margin:0;padding:0;box-sizing:border-box}
html,body{width:750px;height:1200px;overflow:hidden;background:var(--white)}
body{font-family:"Open Sans",sans-serif;color:var(--ink);position:relative}
.serif{font-family:"Merriweather",serif}

.site-header{height:75px;background:var(--navy);display:flex;align-items:center;justify-content:space-between;padding:0 83px}
.brand{display:flex;align-items:center;gap:8px;color:var(--white);font-family:"Merriweather",serif;font-size:15px;letter-spacing:.5px}
.brand-mark{width:14px;height:14px;background:var(--gold)}
.main-nav{display:flex;gap:20px;font-family:"Merriweather",serif;font-size:8px;color:var(--white)}
.main-nav .active{text-decoration:underline}

.hero{position:relative;height:309px;background:linear-gradient(100deg,#5e5750 0%,#8a8076 35%,#b8aea2 60%,#7c7068 100%);text-align:center;color:var(--white)}
.hero-shade{position:absolute;inset:0;background:rgba(20,25,35,.28)}
.hero-inner{position:relative;padding-top:98px}
.play{width:26px;height:26px;margin:0 auto 10px;border-radius:50%;background:var(--white);display:flex;align-items:center;justify-content:center}
.hero h1{font-family:"Merriweather",serif;font-size:20px;font-weight:700}
.hero p{font-size:9.5px;margin-top:8px}
.hero-actions{display:flex;justify-content:center;gap:8px;margin-top:14px}
.btn-light{background:var(--white);color:var(--navy);font-family:"Merriweather",serif;font-size:10px;font-weight:700;height:26px;line-height:26px;padding:0 10px;min-width:106px}
.hero .arrow{position:absolute;top:148px}
.hero .down{position:absolute;left:366px;top:274px}

.partners{height:90px;background:var(--band);display:flex;align-items:center;justify-content:space-around;padding:0 110px;font-weight:600;font-size:13px;color:#444}

.help{text-align:center;padding-top:40px}
.help h2{font-weight:400;font-size:20px;color:var(--muted)}
.help-grid{display:flex;gap:14px;justify-content:center;margin-top:14px}
.help-card{width:187px;height:145px;background:var(--card);padding-top:18px}
.help-card h3{font-family:"Merriweather",serif;font-weight:400;font-size:20px;color:var(--navy);margin-top:6px}
.help-card p{font-size:5.5px;color:#666;line-height:1.5;margin-top:2px}
.btn-navy{display:inline-block;background:var(--navy);color:var(--white);font-size:7px;height:22px;line-height:22px;padding:0 9px;margin-top:7px}

.questions{margin-top:42px;height:150px;background:linear-gradient(180deg,#6d84a8 0%,#8d9bb2 60%,#b9afa8 100%);text-align:center;color:var(--white);padding-top:44px}
.questions h2{font-weight:400;font-size:20px}
.questions .btn-navy{margin-top:9px;font-size:7px;height:25px;line-height:25px}

.team{display:flex;gap:10px;justify-content:center;margin-top:50px}
.member{width:288px;height:110px;background:var(--card);display:flex}
.member-photo{width:110px;height:110px;background:linear-gradient(160deg,#cfcac4,#8b8580)}
.member-body{padding:16px 16px 0 17px}
.member h3{font-family:"Merriweather",serif;font-weight:400;font-size:10px;color:var(--navy)}
.member h4{font-weight:400;font-size:7px;margin-top:5px}
.member p{font-size:6.5px;color:var(--muted);line-height:1.85;margin-top:6px;text-align:justify}

.site-footer{position:absolute;left:0;top:1100px;width:750px;height:100px;background:var(--foot);padding:27px 83px 0;font-size:6px;color:#555}
.foot-left{position:absolute;left:83px;top:27px}
.foot-logos{display:flex;gap:30px;align-items:center;margin-top:12px}
.foot-brand{font-family:"Merriweather",serif;font-size:7px;color:var(--navy-dark);display:flex;align-items:center;gap:4px}
.foot-brand i{width:8px;height:8px;background:var(--navy-dark);display:block}
.badge{width:34px;height:34px;border-radius:50%;background:var(--navy)}
.foot-right{position:absolute;right:83px;top:27px;text-align:right;line-height:2.3}
.social{display:flex;gap:6px;justify-content:flex-end;margin-top:8px}
.social span{width:15px;height:15px;border-radius:50%;background:var(--navy)}
</style>
</head>
<body>
<header class="site-header">
  <div class="brand"><span class="brand-mark"></span>Harborline Lending</div>
  <nav class="main-nav"><span class="active">HOME</span><span>ABOUT</span><span>BLOG</span><span>CONTACT</span></nav>
</header>

<section class="hero" role="img" aria-label="Photo of a mortgage advisor meeting a young couple at a desk with a laptop">
  <div class="hero-shade"></div>
  <svg class="arrow" style="left:14px" width="10" height="16" viewBox="0 0 10 16"><path d="M8 1 2 8l6 7" fill="none" stroke="#fff" stroke-width="1.5"/></svg>
  <svg class="arrow" style="right:14px" width="10" height="16" viewBox="0 0 10 16"><path d="M2 1l6 7-6 7" fill="none" stroke="#fff" stroke-width="1.5"/></svg>
  <div class="hero-inner">
    <div class="play"><svg width="10" height="11" viewBox="0 0 10 11"><path d="M1 0l9 5.5L1 11z" fill="#333"/></svg></div>
    <h1>Morbi elementum vestibulum eget egestas</h1>
    <p>Fusce malesuada ligula efficitur, tempor magna a, interdum nisi</p>
    <div class="hero-actions"><span class="btn-light">GET HOOKED UP</span><span class="btn-light">I'M A CLIENT</span></div>
  </div>
  <svg class="down" width="18" height="16" viewBox="0 0 18 16"><path d="M2 2l7 6 7-6M2 8l7 6 7-6" fill="none" stroke="#fff" stroke-width="1.5"/></svg>
</section>

<section class="partners">
  <span>Tidal</span><span>Brisk</span><span>Ember</span><span>Northwave</span><span>Lumen</span><span>Velta</span>
</section>

<section class="help">
  <h2>I need help with</h2>
  <div class="help-grid">
    <article class="help-card">
      <svg width="28" height="26" viewBox="0 0 28 26"><path d="M1 2h5l4 14h13l3-10H8" fill="none" stroke="#0a3a80" stroke-width="3"/><circle cx="11" cy="22" r="2.5" fill="#0a3a80"/><circle cx="21" cy="22" r="2.5" fill="#0a3a80"/></svg>
      <h3>Purchase</h3>
      <p>Maecenas vitae eros ut nisl fermentum rutrum.<br>Suspendisse in semper purus, sapien.</p>
      <span class="btn-navy">CONTACT US</span>
    </article>
    <article class="help-card">
      <svg width="32" height="26" viewBox="0 0 32 26"><rect x="1.5" y="3.5" width="29" height="19" fill="none" stroke="#0a3a80" stroke-width="3"/><circle cx="16" cy="13" r="6" fill="#0a3a80"/><path d="M16 10v6" stroke="#fff" stroke-width="2"/></svg>
      <h3>Refinance</h3>
      <p>Maecenas vitae eros ut nisl fermentum rutrum.<br>Suspendisse in semper purus, sapien.</p>
      <span class="btn-navy">CONTACT US</span>
    </article>
    <article class="help-card">
      <svg width="28" height="26" viewBox="0 0 28 26"><path d="M4 11a10 10 0 0 1 18-4M24 15a10 10 0 0 1-18 4" fill="none" stroke="#0a3a80" stroke-width="3.5"/><path d="M19 2l6 1-1 6zM9 24l-6-1 1-6z" fill="#0a3a80"/></svg>
      <h3>Renew</h3>
      <p>Maecenas vitae eros ut nisl fermentum rutrum.<br>Suspendisse in semper purus, sapien.</p>
      <span class="btn-navy">CONTACT US</span>
    </article>
  </div>
</section>

<section class="questions" role="img" aria-label="Soft evening sky background">
  <h2>Mortgage or Real Estate Questions?</h2>
  <span class="btn-navy">ASK QUESTIONS</span>
</section>

<section class="team">
  <article class="member">
    <div class="member-photo" role="img" aria-label="Portrait photo of a male advisor in a suit"></div>
    <div class="member-body">
      <h3>Mark Ellison</h3>
      <h4>Etiam rutrum maximus luctus</h4>
      <p>Ullamcorper aliquet elit massa at neque. Fusce malesuada ligula efficitur, tempor magna a, interdum nisi. Vivamus ultricies justo ut commodo egestas.</p>
    </div>
  </article>
  <article class="member">
    <div class="member-photo" role="img" aria-label="Portrait photo of a smiling female advisor" style="background:linear-gradient(160deg,#f2efea,#c9bba8)"></div>
    <div class="member-body">
      <h3>Mark Ellison</h3>
      <h4>Etiam rutrum maximus luctus</h4>
      <p>Ullamcorper aliquet elit massa at neque. Fusce malesuada ligula efficitur, tempor magna a, interdum nisi. Vivamus ultricies justo ut commodo egestas.</p>
    </div>
  </article>
</section>

<footer class="site-footer">
  <div class="foot-left">
    <div>Copyright © 2017 Colin Ashford. All rights reserved.</div>
    <div class="foot-logos">
      <span class="foot-brand"><i></i>Harborline Lending</span>
      <span class="badge"></span>
    </div>
  </div>
  <div class="foot-right">
    <div>&#9679; 48 Cedarline Ave. Northgate, BC V0N 1A0</div>
    <div>E-mail : colin@harborlinehomes.ca &nbsp;|&nbsp; Phone : 555.014.2287</div>
    <div class="social"><span></span><span></span><span></span><span></span></div>
  </div>
</footer>
</body>
</html>
```